Simple and Clean business card design

We would like the design to be simple clean and to incorporate our colors.

We are open to your design and talent, we have the dots in our logo as we think of it as data points and we connect data points for people.

We are open to see the great creative and clean design you bring to the table

Contact Information for Business Card

please include: name, position, email, phone and website

Font styles to use
Sans Serif

Requirements
Must have
• my colors incorporated, simplicity
Nice to have
• lots of white space, simplicity
Should not have
• complexicity/ complex art

```html
<!DOCTYPE html>
<html lang="en">
<head>
<meta charset="utf-8">
<title>Lumora business card</title>
<link rel="stylesheet" href="https://fonts.googleapis.com/css2?family=Montserrat:wght@500&family=Nunito+Sans:wght@400;800&display=swap">
<style>
  :root {
    --backdrop: #9a9a9a;
    --card: #ffffff;
    --ink: #161616;
    --text: #333333;
    --green: #34a853;
    --blue: #5f86c4;
    --faint-blue: #eff3f9;
  }
  * { margin: 0; padding: 0; box-sizing: border-box; }
  html, body {
    width: 1021px; height: 1200px; overflow: hidden;
    background: var(--backdrop);
    font-family: "Nunito Sans", Arial, sans-serif;
  }
  .card {
    position: absolute;
    width: 753px; height: 429px;
    background: var(--card);
  }
  .card--front { left: 134px; top: 119px; }
  .card--back { left: 131px; top: 651px; }

  .wordmark {
    position: absolute;
    display: flex; align-items: center;
    font-family: "Montserrat", Arial, sans-serif;
    font-weight: 500;
    color: var(--ink);
    line-height: 1;
  }
  .wordmark__dot { border-radius: 50%; background: var(--green); flex: none; }
  .card--front .wordmark {
    left: 0; right: 0; top: 155px; justify-content: center; gap: 18px;
    font-size: 128px; letter-spacing: 2px;
  }
  .card--front .wordmark__dot { width: 40px; height: 40px; }
  .card--back .wordmark {
    left: 30px; top: 88px; gap: 10px;
    font-size: 70px; letter-spacing: 1px;
  }
  .card--back .wordmark__dot { width: 22px; height: 22px; }

  .deco-ring {
    position: absolute; left: 419px; top: 188px;
    width: 141px; height: 141px; border-radius: 50%;
    border: 17px solid var(--faint-blue);
  }
  .accent-bar {
    position: absolute; left: 0; top: 264px;
    width: 17px; height: 43px; background: var(--blue);
  }
  .company {
    position: absolute; left: 32px; top: 262px;
    font-size: 26px; font-weight: 800; letter-spacing: 0.5px;
    color: var(--green);
  }
  .company__tld { color: var(--blue); }
  .role {
    position: absolute; left: 32px; top: 290px;
    font-size: 18px; color: var(--text);
  }
  .rule {
    position: absolute; left: 160px; top: 301px;
    width: 558px; height: 1.5px; background: var(--blue);
  }
  .contacts {
    position: absolute; left: 31px; top: 322px;
    list-style: none;
  }
  .contacts li {
    display: flex; align-items: center; gap: 8px;
    height: 27px;
    font-size: 19px; color: var(--text);
  }
  .contacts svg { width: 15px; height: 15px; fill: var(--green); flex: none; }
</style>
</head>
<body>

<section class="card card--front">
  <div class="wordmark"><span class="wordmark__dot"></span>Lumora</div>
</section>

<section class="card card--back">
  <div class="wordmark"><span class="wordmark__dot"></span>Lumora</div>
  <div class="deco-ring"></div>

  <div class="accent-bar"></div>
  <div class="company">LUMORA<span class="company__tld">.IO</span></div>
  <div class="role">Founder/ CEO</div>
  <div class="rule"></div>

  <ul class="contacts">
    <li>
      <svg viewBox="0 0 16 16" aria-hidden="true"><path d="M3.5 1l2.5 3-1.5 1.8c.9 2 2.3 3.4 4.2 4.3L10.5 8.5l3 2.5-1.5 3C6.5 13.5 2.5 9.5 2 3.5z"/></svg>
      555-014-2298
    </li>
    <li>
      <svg viewBox="0 0 16 16" aria-hidden="true"><path d="M1 3h14v10H1z M2.5 4.2L8 8.6l5.5-4.4v.9L8 9.6 2.5 5.1z" fill-rule="evenodd"/></svg>
      dana.wells@lumora.io
    </li>
    <li>
      <svg viewBox="0 0 16 16" aria-hidden="true"><circle cx="8" cy="8" r="7"/><path d="M4 4.5c1.5.2 2 1.2 1.5 2.3-.6 1 .6 1.6.5 2.8-.1 1-1 1.4-1 2.6M10 2.5c-.5 1.3.5 2 1.6 1.8M11 8.5c-1 .3-1.5 1.3-.8 2.3" stroke="#fff" stroke-width="1.1" fill="none"/></svg>
      www.Lumora.io
    </li>
  </ul>
</section>

</body>
</html>
```